Brivane Management

We need a web design for a new consulting company, with clients all over the world. The company provides management consulting to the travel industry.

Logo files are attached.

Website must look very corporate and be responsive in design.

Management Consulting

```html
<!DOCTYPE html>
<html lang="en">
<head>
<meta charset="utf-8">
<title>Brivane Strategy Management</title>
<link rel="stylesheet" href="https://fonts.googleapis.com/css2?family=Cinzel:wght@400;700&family=Bitter:wght@400&family=Open+Sans:ital,wght@0,300;0,400;0,600;0,700;1,400&family=Roboto:wght@500;700&display=swap">
<style>
:root{
  --navy:#0b1a3a;
  --blue:#1668bd;
  --blue-light:#3a93e0;
  --green:#6dbb1f;
  --ink:#2b2b2b;
  --text:#555;
  --muted:#8a8a8a;
  --line:#d9d9d9;
  --panel:#ffffff;
  --page:#e6e6e6;
  --soft:#f3f3f3;
  --footer-deep:#121212;
}
*{box-sizing:border-box;margin:0;padding:0}
html,body{width:800px;height:1200px;overflow:hidden}
body{position:relative;background:var(--page);font-family:"Open Sans",sans-serif;color:var(--text)}
.abs{position:absolute}
.top-stripe{left:0;top:0;width:800px;height:5px;background:var(--navy)}
.header{left:0;top:5px;width:800px;height:65px;background:linear-gradient(#fff,#eef0f2)}
.brand{left:90px;top:14px;display:flex;align-items:center;gap:8px}
.brand-dot{width:44px;height:44px;border-radius:50%;background:var(--blue)}
.brand-name{font-family:"Open Sans",sans-serif;font-weight:700;color:var(--navy);line-height:1}
.brand-name .big{display:block;font-size:27px;letter-spacing:1px}
.brand-name .small{display:block;font-size:10.5px;letter-spacing:1.4px;margin-top:4px}
.help{left:603px;top:24px;display:flex;gap:8px;align-items:center}
.help-icon{width:25px;height:25px;border-radius:4px;background:#333;display:flex;align-items:center;justify-content:center}
.help small{display:block;font-size:8px;color:var(--muted);font-weight:600;letter-spacing:.5px}
.help strong{display:block;font-size:13px;color:#333;font-weight:700}
.nav{left:0;top:70px;width:800px;height:29px;background:linear-gradient(var(--blue-light),var(--blue))}
.nav-item{top:70px;height:29px;line-height:29px;text-align:center;font-family:"Cinzel",serif;font-size:12px;color:#fff;border-right:1px solid rgba(255,255,255,.25)}
.nav-item.active{background:var(--green)}
.search{left:578px;top:73px;width:132px;height:23px;background:#fff;border-radius:2px;font-size:8px;color:#aaa;padding:6px 7px}
.search-btn{left:686px;top:73px;width:24px;height:23px;background:#333;border-radius:0 2px 2px 0;display:flex;align-items:center;justify-content:center}
.hero{left:0;top:99px;width:800px;height:255px;background:linear-gradient(90deg,#9aa7b0 0%,#c9cfd3 35%,#b6c0c6 60%,#8d8f92 100%)}
.hero-arrow{top:203px;width:22px;height:22px;border-radius:50%;background:rgba(0,0,0,.25)}
.hero-caption{left:0;top:323px;width:800px;height:31px;background:rgba(20,20,20,.55);color:#fff;font-family:"Bitter",serif;font-size:18px;text-align:center;line-height:31px;padding-left:22px}
.panel{left:88px;top:354px;width:626px;height:601px;background:var(--panel);box-shadow:0 0 4px rgba(0,0,0,.15)}
.card{top:373px;width:188px;height:176px;border:1px solid var(--line);border-radius:6px;background:#fff;overflow:hidden;box-shadow:0 6px 6px -4px rgba(0,0,0,.12)}
.card-head{height:33px;background:linear-gradient(#fff,#eee);border-bottom:1px solid var(--line);display:flex;align-items:center;gap:6px;padding-left:8px;font-family:"Roboto",sans-serif;font-weight:700;font-size:13px;color:#333}
.card-head em{font-style:normal;color:var(--green)}
.head-dot{width:22px;height:22px;border-radius:50%;background:var(--blue)}
.card-body{padding:6px 7px;font-size:8px;line-height:12px;color:#444;letter-spacing:-.1px}
.corner{right:0;bottom:0;width:28px;height:28px}
.news{display:flex;gap:8px;padding:0 0 6px;margin-bottom:6px;border-bottom:1px dashed #ccc}
.news:last-child{border:0}
.date{width:21px;flex:none;text-align:center;font-size:7px;font-weight:700;color:#fff;line-height:10px}
.date span{display:block;background:#777}
.date span+span{background:#444}
.news b{display:block;font-size:8.2px;color:#222;margin-bottom:2px}
.field{width:173px;border:1px solid #ccc;border-radius:2px;font-size:8.4px;color:#777;padding:4px 6px;margin-bottom:4px;height:22px;box-shadow:inset 0 1px 2px rgba(0,0,0,.08)}
.field.tall{height:52px}
.services-area{left:88px;top:583px;width:626px;height:265px;background:var(--soft)}
.services-tab{left:326px;top:583px;width:140px;height:21px;background:linear-gradient(#fff,#e4e4e4);clip-path:polygon(0 0,100% 0,92% 100%,8% 100%);text-align:center;font-family:"Roboto",sans-serif;font-weight:700;font-size:13px;line-height:21px;color:#333}
.services-tab em{font-style:normal;color:var(--green)}
.service{width:290px;height:56px}
.service::before{content:"";position:absolute;left:0;top:0;width:290px;height:1px;background:linear-gradient(90deg,#ddd,transparent)}
.svc-icon{left:11px;top:0;width:56px;height:48px;background:linear-gradient(#fff,#dcdcdc);border:1px solid #d2d2d2;border-top:2px solid var(--green);border-radius:0 0 4px 4px;display:flex;align-items:center;justify-content:center}
.svc-title{left:78px;top:4px;font-family:"Roboto",sans-serif;font-weight:500;font-size:12px;color:#222;white-space:nowrap}
.svc-text{left:78px;top:20px;width:218px;font-size:8.2px;line-height:12px;color:#444}
.testimonial{left:88px;top:848px;width:626px;height:107px;background:#ebebeb}
.avatar{left:106px;top:868px;width:57px;height:57px;border-radius:50%;background:linear-gradient(#c9d3dc,#8896a3);border:3px solid #fff;box-shadow:0 0 2px rgba(0,0,0,.3)}
.quote{left:190px;top:870px;width:500px;font-size:8.4px;line-height:14px;font-style:italic;color:#444}
.quote-mark{font-family:"Bitter",serif;font-size:28px;color:#bbb;line-height:1}
.quote-rule{left:188px;top:920px;width:500px;height:1px;background:#ccc}
.author{left:192px;top:926px;font-size:9px;font-weight:700;color:var(--blue)}
.dots{left:648px;top:933px;display:flex;gap:3px}
.dots i{width:6px;height:6px;border-radius:50%;background:#ccc}
.dots i:first-child{background:var(--green)}
.footer{left:0;top:955px;width:800px;height:215px;background:linear-gradient(#262626,var(--footer-deep))}
.newsletter{left:95px;top:967px;width:611px;height:41px;background:var(--footer-deep);border-radius:3px}
.nl-title{left:108px;top:975px;font-size:18px;font-weight:300;color:#fff}
.nl-div{left:258px;top:973px;width:1px;height:29px;background:#3a3a3a}
.nl-copy{left:272px;top:975px;width:150px;font-size:8.5px;line-height:13px;color:#ddd}
.nl-input{left:427px;top:978px;width:188px;height:20px;background:#fff;border-radius:2px;font-size:8px;color:#888;padding:5px 7px}
.nl-btn{left:620px;top:978px;width:76px;height:20px;background:var(--green);border-radius:2px;color:#fff;font-weight:700;font-size:10px;text-align:center;line-height:20px}
.foot-head{top:1041px;font-family:"Roboto",sans-serif;font-weight:500;font-size:12px;color:#fff}
.link{font-size:8.5px;color:#ddd;width:80px;padding:0 0 10px 12px;border-bottom:1px solid #2e2e2e}
.link::before{content:"›";position:absolute;left:2px;top:-1px;color:#666}
.contact-row{left:320px;width:190px;display:flex;gap:10px;font-size:8.5px;line-height:12px;color:#ddd}
.contact-row svg{flex:none;margin-top:1px}
.col-rule{top:1030px;width:1px;height:130px;background:#2e2e2e}
.foot-brand{left:545px;top:1058px;width:155px;text-align:center;color:#fff;font-weight:700;line-height:1}
.foot-brand .dot{width:40px;height:40px;border-radius:50%;background:#fff;margin:0 auto 12px}
.foot-brand .big{display:block;font-size:23px;letter-spacing:1px}
.foot-brand .small{display:block;font-size:8.5px;letter-spacing:1px;margin-top:4px}
.bottom-bar{left:0;top:1170px;width:800px;height:30px;background:#2b2b2b}
.copyright{left:102px;top:1180px;font-size:7.5px;color:#ddd}
.follow{left:555px;top:1178px;font-size:10px;color:#fff;letter-spacing:.5px}
.social{top:1175px;width:19px;height:19px;border-radius:50%;background:#fff}
.social.on{background:var(--green)}
</style>
</head>
<body>
<div class="abs top-stripe"></div>

<header class="abs header"></header>
<div class="abs brand">
  <div class="brand-dot"></div>
  <div class="brand-name"><span class="big">BRIVANE</span><span class="small">STRATEGY MANAGEMENT, INC.</span></div>
</div>
<div class="abs help">
  <div class="help-icon"><svg width="13" height="13" viewBox="0 0 24 24"><path fill="#fff" d="M6.6 10.8a15 15 0 006.6 6.6l2.2-2.2c.3-.3.7-.4 1-.2 1.1.4 2.3.6 3.6.6.6 0 1 .4 1 1V20c0 .6-.4 1-1 1A17 17 0 013 4c0-.6.4-1 1-1h3.5c.6 0 1 .4 1 1 0 1.3.2 2.5.6 3.6.1.3 0 .7-.2 1z"/></svg></div>
  <div><small>HAPPY TO HELP?</small><strong>010-555-0147</strong></div>
</div>

<nav class="abs nav"></nav>
<div class="abs nav-item active" style="left:90px;width:67px">HOME</div>
<div class="abs nav-item" style="left:160px;width:79px">ABOUT</div>
<div class="abs nav-item" style="left:240px;width:87px">SERVICES</div>
<div class="abs nav-item" style="left:328px;width:99px">RESOURCES</div>
<div class="abs nav-item" style="left:428px;width:90px">CONTACT</div>
<div class="abs search">search...</div>
<div class="abs search-btn"><svg width="11" height="11" viewBox="0 0 12 12"><circle cx="5" cy="5" r="3.5" fill="none" stroke="#fff" stroke-width="1.5"/><path d="M7.5 7.5L11 11" stroke="#fff" stroke-width="1.8"/></svg></div>

<div class="abs hero" role="img" aria-label="Photo of a smiling businessman handing a document to a businesswoman at a travel office counter"></div>
<div class="abs hero-arrow" style="left:57px"></div>
<div class="abs hero-arrow" style="left:724px"></div>
<div class="abs hero-caption">We Provides Management Consulting to the Travel Industry</div>

<main class="abs panel"></main>

<section class="abs card" style="left:100px">
  <div class="card-head"><span class="head-dot"></span><span>ABOUT <em>BRIVANE</em></span></div>
  <p class="card-body">Lorem diam nonummy nibh esmod tincidu uta oreet dolore magna quam eratlutpat.nim ad minim veniam, quis nostrud nim adminim veniam, quis nostrud tationau ulamcorper scipit lortis nisl utnim ad minima veniarwem, quis nostrud exercin ulamco suscipit lobortis nisl utnim nim veniam, quis nostrud exerci scipit lortis nisl utnim ad minima veniarwem, nisl utnim nim veniam, quis nostrud exerci tation ulamcorper suscipit</p>
  <svg class="abs corner" viewBox="0 0 28 28"><path d="M28 0V28H0Z" fill="#1a74cc"/><path d="M18 20h8M22 16v8" stroke="#fff" stroke-width="2"/></svg>
</section>

<section class="abs card" style="left:307px">
  <div class="card-head"><span class="head-dot"></span><span>LATEST <em>NEWS</em></span></div>
  <div class="card-body">
    <div class="news"><div class="date"><span>09</span><span>OCT</span></div><div><b>Lorem ipsum dolor sit amet</b>is nisl utnim ad minima venam, quis nostrud exercin ulamcocipit lobortis nisl utnim nim veniam,is nisl utnimi ad minima veniam, quis</div></div>
    <div class="news"><div class="date"><span>09</span><span>OCT</span></div><div><b>Lorem ipsum dolor sit amet</b>Lorem ipsum smet consectetur mini adipisic elitsed do eit eim adosi miie vnioremipsuma</div></div>
  </div>
  <svg class="abs corner" viewBox="0 0 28 28"><path d="M28 0V28H0Z" fill="#1a74cc"/><path d="M18 20h8M22 16v8" stroke="#fff" stroke-width="2"/></svg>
</section>

<section class="abs card" style="left:514px">
  <div class="card-head"><span class="head-dot"></span><span>QUICK <em>CONTACT</em></span></div>
  <div class="card-body" style="padding-top:10px">
    <div class="field">Name</div>
    <div class="field">Email</div>
    <div class="field tall">Message</div>
  </div>
  <svg class="abs corner" viewBox="0 0 28 28"><path d="M28 0V28H0Z" fill="#1a74cc"/><path d="M18 20h8M22 16v8" stroke="#fff" stroke-width="2"/></svg>
</section>

<div class="abs services-area"></div>
<div class="abs services-tab">OUR <em>SERVICES</em></div>

<div class="abs service" style="left:100px;top:624px">
  <div class="abs svc-icon"><svg width="34" height="34" viewBox="0 0 34 34"><rect x="4" y="22" width="4" height="8" fill="#222"/><rect x="10" y="18" width="4" height="12" fill="#222"/><rect x="16" y="14" width="4" height="16" fill="#222"/><rect x="22" y="10" width="4" height="20" fill="#222"/><path d="M5 18L25 5" stroke="#1a74cc" stroke-width="3"/><path d="M19 3h9v8z" fill="#1a74cc"/></svg></div>
  <div class="abs svc-title">Sales/ Marketing</div>
  <p class="abs svc-text">Lorem ipsum dolor sit amet consectetur elitsed do eiusmod tempor incididunt ut labore et dolore magna aliqua ut enim ad minim vesniam.</p>
</div>
<div class="abs service" style="left:417px;top:624px">
  <div class="abs svc-icon"><svg width="34" height="34" viewBox="0 0 34 34"><circle cx="13" cy="9" r="6" fill="#222"/><path d="M2 30c0-9 5-13 11-13s11 4 11 13z" fill="#222"/><circle cx="24" cy="24" r="7" fill="#fff" stroke="#1a74cc" stroke-width="2.5"/><path d="M24 20v4h3" stroke="#1a74cc" stroke-width="2" fill="none"/></svg></div>
  <div class="abs svc-title">Strategic Planning</div>
  <p class="abs svc-text">Lorem ipsum dolor sit amet consectetur elitsed do eiusmod tempor incididunt ut labore et dolore magna aliqua ut enim ad minim vesniam.</p>
</div>
<div class="abs service" style="left:100px;top:696px">
  <div class="abs svc-icon"><svg width="34" height="34" viewBox="0 0 34 34"><circle cx="12" cy="6" r="4" fill="#222"/><path d="M6 12h12v10h-3v10h-6V22H6z" fill="#222"/><circle cx="22" cy="22" r="8" fill="#fff" stroke="#1a74cc" stroke-width="2.5"/><text x="22" y="26.5" font-size="12" font-weight="700" text-anchor="middle" fill="#1a74cc" font-family="Open Sans,sans-serif">$</text></svg></div>
  <div class="abs svc-title">Human Capital Management Solutions</div>
  <p class="abs svc-text">Lorem ipsum dolor sit amet consectetsed do eiusmod tempor incididunt ut labore et dolore magna aliqua ut enim ad minim vesniam.</p>
</div>
<div class="abs service" style="left:417px;top:696px">
  <div class="abs svc-icon"><svg width="34" height="34" viewBox="0 0 34 34"><rect x="3" y="5" width="24" height="19" fill="none" stroke="#222" stroke-width="2.5"/><path d="M6 19l5-6 4 4 5-7 4 4" stroke="#222" stroke-width="2" fill="none"/><circle cx="23" cy="22" r="5" fill="#fff" stroke="#1a74cc" stroke-width="2.5"/><path d="M27 26l4 4" stroke="#1a74cc" stroke-width="3"/></svg></div>
  <div class="abs svc-title">Financial Analysis</div>
  <p class="abs svc-text">Lorem ipsum dolor sit amet consectetur elitsed do eiusmod tempor incididunt ut labore et dolore magna aliqua ut enim ad minim vesniam.</p>
</div>
<div class="abs service" style="left:100px;top:775px">
  <div class="abs svc-icon"><svg width="34" height="34" viewBox="0 0 34 34"><path d="M12 9V6h10v3" stroke="#222" stroke-width="2.5" fill="none"/><rect x="3" y="9" width="28" height="19" rx="2" fill="#222"/><rect x="15" y="15" width="4" height="4" fill="#fff"/><circle cx="27" cy="26" r="5" fill="#1a74cc"/><text x="27" y="29" font-size="8" font-weight="700" text-anchor="middle" fill="#fff" font-family="Open Sans,sans-serif">$</text></svg></div>
  <div class="abs svc-title">Cash Management Solutions</div>
  <p class="abs svc-text">Lorem ipsum dolor sit amet consectetur elitsed do eiusmod tempor incididunt ut labore et dolore magna aliqua ut enim ad minim vesniam.</p>
</div>
<div class="abs service" style="left:417px;top:775px">
  <div class="abs svc-icon"><svg width="34" height="34" viewBox="0 0 34 34"><path d="M6 20v-4a11 11 0 0122 0v4" stroke="#222" stroke-width="3" fill="none"/><rect x="4" y="17" width="6" height="10" rx="2" fill="#222"/><rect x="24" y="17" width="6" height="10" rx="2" fill="#222"/><path d="M27 27c0 3-4 4-8 4" stroke="#1a74cc" stroke-width="2" fill="none"/><circle cx="18" cy="31" r="2" fill="#1a74cc"/></svg></div>
  <div class="abs svc-title">Customer Support</div>
  <p class="abs svc-text">Lorem ipsum dolor sit amet consectetur elitsed do eiusmod tempor incididunt ut labore et dolore magna aliqua ut enim ad minim vesniam.</p>
</div>

<section class="abs testimonial"></section>
<div class="abs avatar" role="img" aria-label="Portrait photo of the client giving the testimonial"></div>
<div class="abs quote-mark" style="left:177px;top:862px">&ldquo;</div>
<p class="abs quote">Lorem ipsum dolor sit amet consectetur adipisicing elitsed do eiusmod tempor incididunt ut labore et dolore magna aliqua. Ut enim ad minim vesniam, quis nostrud exercitation ullamco laboris nisi ut aliquip ex ea commodo consequat. Duis aute irure dolor in reprehenderit in voluptate velit esse cillum is a dolore eu fugiat nulla pariatur. Excepteur sint occaecat cupidatat non proi</p>
<div class="abs quote-mark" style="left:692px;top:898px">&rdquo;</div>
<div class="abs quote-rule"></div>
<div class="abs author">Daniel Harper</div>
<div class="abs dots"><i></i><i></i><i></i><i></i></div>

<footer class="abs footer"></footer>
<div class="abs newsletter"></div>
<div class="abs nl-title">Newsletter Signup</div>
<div class="abs nl-div"></div>
<p class="abs nl-copy">Get latest updates by entering your email address.</p>
<div class="abs nl-input">Enter your Email...</div>
<div class="abs nl-btn">SUBSCRIBE</div>

<div class="abs foot-head" style="left:102px">QUICK LINKS</div>
<div class="abs link" style="left:106px;top:1072px">Home</div>
<div class="abs link" style="left:106px;top:1101px">Services</div>
<div class="abs link" style="left:106px;top:1131px">Contact Us</div>
<div class="abs link" style="left:205px;top:1075px">About Us</div>
<div class="abs link" style="left:205px;top:1101px">Resources</div>
<div class="abs col-rule" style="left:300px"></div>

<div class="abs foot-head" style="left:320px">CONTACT US</div>
<div class="abs contact-row" style="top:1075px"><svg width="9" height="12" viewBox="0 0 9 12"><path d="M4.5 0A4.5 4.5 0 000 4.5C0 8 4.5 12 4.5 12S9 8 9 4.5A4.5 4.5 0 004.5 0z" fill="#fff"/><circle cx="4.5" cy="4.5" r="1.6" fill="#1c1c1c"/></svg><span>Lorem ipsum dolor sit amet consecttuer adi piscing elit diam non</span></div>
<div class="abs contact-row" style="top:1107px"><svg width="10" height="10" viewBox="0 0 24 24"><path fill="#fff" d="M6.6 10.8a15 15 0 006.6 6.6l2.2-2.2c.3-.3.7-.4 1-.2 1.1.4 2.3.6 3.6.6.6 0 1 .4 1 1V20c0 .6-.4 1-1 1A17 17 0 013 4c0-.6.4-1 1-1h3.5c.6 0 1 .4 1 1 0 1.3.2 2.5.6 3.6.1.3 0 .7-.2 1z"/></svg><span>010-555-0147</span></div>
<div class="abs contact-row" style="top:1127px"><svg width="10" height="8" viewBox="0 0 10 8"><rect width="10" height="8" fill="#fff"/><path d="M0 0l5 4 5-4" stroke="#1c1c1c" fill="none"/></svg><span>info@brivanestrategy.com</span></div>
<div class="abs col-rule" style="left:524px"></div>

<div class="abs foot-brand">
  <div class="dot"></div>
  <span class="big">BRIVANE</span><span class="small">STRATEGY MANAGEMENT, INC.</span>
</div>

<div class="abs bottom-bar"></div>
<div class="abs copyright">Copyright 2014 <b>brivanestrategymanagement.</b> All Right Reserved.</div>
<div class="abs follow">FOLLOW US :</div>
<div class="abs social on" style="left:618px"></div>
<div class="abs social" style="left:643px"></div>
<div class="abs social" style="left:667px"></div>
<div class="abs social" style="left:691px"></div>
</body>
</html>
```